Commercial Real Estate Property Sign

Design a 4' x 4' sign that pops. Refer to examples.

Must include the following information:
A space to list (For Sale, For Lease, Build-to-Suite or Available)
BrightKeel,LLC
Commercial Real Estate
company website
My Name (Marcus Pellow)
My Phone #

Industry/Entity Type

Real Estate

```html
<!DOCTYPE html>
<html lang="en">
<head>
<meta charset="UTF-8">
<title>BrightKeel LLC – Space for Lease Sign</title>
<link rel="stylesheet" href="https://fonts.googleapis.com/css2?family=Barlow:wght@400;500;700;800&display=swap">
<style>
  :root {
    --charcoal: #3b3b3c;
    --orange: #e96506;
    --ink: #1f1f1f;
    --white: #ffffff;
    --black: #000000;
  }
  * { margin: 0; padding: 0; box-sizing: border-box; }
  html, body { width: 1200px; height: 1200px; overflow: hidden; }
  body { font-family: "Barlow", Arial, sans-serif; background: var(--orange); }

  .sign { position: relative; width: 1200px; height: 1200px; background: var(--orange); }

  .header-band {
    position: absolute; left: 0; top: 0; width: 1200px; height: 273px;
    background: var(--charcoal);
  }
  .brand-square {
    position: absolute; left: 37px; top: 53px; width: 54px; height: 114px;
    background: var(--black);
  }
  .brand-name {
    position: absolute; left: 0; top: 48px; width: 1200px; text-align: center;
    font-weight: 500; font-size: 100px; line-height: 120px;
    letter-spacing: 14px; color: var(--white);
  }
  .tagline {
    position: absolute; left: 0; top: 178px; width: 1200px; height: 50px;
    display: flex; align-items: center; gap: 22px;
  }
  .tagline-rule { flex: 1; height: 3px; background: var(--orange); }
  .tagline-text {
    font-weight: 500; font-size: 42px; color: var(--white); letter-spacing: 1px;
    white-space: nowrap;
  }

  .listing-band {
    position: absolute; left: 0; top: 411px; width: 1200px; height: 198px;
    background: var(--charcoal);
    display: flex; align-items: center; justify-content: center;
  }
  .listing-status {
    font-weight: 800; font-size: 100px; color: var(--white); white-space: nowrap;
  }
  .listing-status .accent { color: var(--orange); font-size: 116px; }

  .agent-name {
    position: absolute; left: 0; top: 720px; width: 1200px; text-align: center;
    font-weight: 500; font-size: 86px; line-height: 100px; color: var(--ink);
  }
  .agent-phone {
    position: absolute; left: 0; top: 868px; width: 1200px; text-align: center;
    font-weight: 800; font-size: 122px; line-height: 130px; color: var(--ink);
    letter-spacing: 2px;
  }
  .website {
    position: absolute; left: 0; top: 1062px; width: 1200px;
    display: flex; align-items: center; justify-content: center; gap: 14px;
    font-weight: 800; font-size: 70px; line-height: 86px; color: var(--ink);
  }
  .website-icon { width: 58px; height: 58px; }
</style>
</head>
<body>
  <main class="sign">
    <header class="header-band">
      <div class="brand-square"></div>
      <div class="brand-name">BrightKeel LLC</div>
      <div class="tagline">
        <span class="tagline-rule"></span>
        <span class="tagline-text">Commercial Real Estate</span>
        <span class="tagline-rule"></span>
      </div>
    </header>

    <section class="listing-band">
      <h1 class="listing-status"><span class="accent">F</span>or Space for <span class="accent">L</span>ease</h1>
    </section>

    <p class="agent-name">Marcus Pellow</p>
    <p class="agent-phone">469.555.0182</p>

    <p class="website">
      <svg class="website-icon" viewBox="0 0 60 60" fill="none" stroke="#1f1f1f" stroke-width="4" aria-hidden="true">
        <circle cx="30" cy="30" r="26"/>
        <ellipse cx="30" cy="30" rx="11" ry="26"/>
        <line x1="4" y1="30" x2="56" y2="30"/>
        <path d="M9 17 H51 M9 43 H51"/>
      </svg>
      <span>www.MyBrightKeel.com</span>
    </p>
  </main>
</body>
</html>
```